Website with a rustic Patriotic Feel

I am looking to design the
Home page I have a mock-up that has the essentials on it like our video, a small slideshow, our plans, and a coverage map, and a small sign up box to be sent a free SIM card.

Eligibility Page: Cool Background with a fill in box that lets the user know if their number is GSM or unlocked.

View Plans page: will have our plans hopefully in their colors with a cool background a walkthrough on Activation.

Activation: If you order your plan first then we send the SIM Card Basically another fill out sheet first name last name ICCID IMEI phone number email

, Contact Us: This is our Customer support page.

Steady Beacon ( this will be our About us page and will have a calendar of Community Volunteer Opportunities.. Right now I have a hodgepodge of different themes that I am going with for the web design. I would like it cohesive with the theme so all of it can fit together nicely.

At the Site map at the bottom we are looking for the basic Menu redirects. quick links to our T&Cs Customer Support and Follow US Buttons as well as a sign up for our Newsletter fill in.

Feel free to redo any of the ads. We are an MVNO like (Northpine Wireless) we provide network Voice and Data Plans our target audience is first Responders and Military. If you are wondering what that green map is its a coverage map to see where to best have coverage. Right now I have a website that uses CMS and HTML. If you are interested in doing a full redesign of our website we would love it.

Right now our website is www.tallow-linkwave.example if you need any additional information.

Target Market(s)

First Responders and Military

Coding

Coded - Design and coding required

Number of Pages Required

5+ page

Font styles to use
Sans Serif

Colors
0455a3
0493ce
f0474d
ffffff

Requirements
Must have
• Cohesive and have a powerpoint and coverage map
Should not have
• Anything flowery or kiddish

```html
<!DOCTYPE html>
<html lang="en">
<head>
<meta charset="utf-8">
<title>Tallow Linkwave Mobile Services</title>
<link rel="stylesheet" href="https://fonts.googleapis.com/css2?family=Montserrat:wght@300;400;600;700;800&family=Nunito+Sans:wght@400;600;700&display=swap">
<style>
:root{
  --navy:#0b2452;
  --navy-deep:#0c2c6e;
  --blue:#0455a3;
  --sky:#0493ce;
  --red:#e8333f;
  --coral:#f0474d;
  --white:#ffffff;
  --ink:#3b3b3b;
  --parchment:#e6cf9c;
  --parchment-light:#f3e6c6;
  --bronze:#b2704f;
  --silver:#cfcfcf;
  --gold:#c7a22c;
  --platinum:#1b9fe0;
  --diamond:#0f3f8c;
}
*{box-sizing:border-box;margin:0;padding:0}
html,body{width:1200px;height:3244px;overflow:hidden}
body{position:relative;font-family:"Nunito Sans",Arial,sans-serif;color:var(--ink);background:var(--white)}
.abs{position:absolute}
.heading{font-family:"Montserrat",Arial,sans-serif}

/* header */
.site-header{position:absolute;left:0;top:0;width:1200px;height:106px;background:var(--navy)}
.brand{position:absolute;left:100px;top:34px;display:flex;align-items:center;gap:10px;font-family:"Montserrat",Arial,sans-serif;font-weight:800;font-size:22px;color:var(--white);letter-spacing:1px}
.brand-dot{width:34px;height:34px;border-radius:50%;background:var(--sky)}
.main-nav{position:absolute;left:347px;top:0;height:106px;display:flex;gap:38px;align-items:center;font-family:"Montserrat",Arial,sans-serif;font-size:14px;color:var(--white)}
.main-nav a{color:inherit;text-decoration:none;position:relative;height:106px;display:flex;align-items:center}
.main-nav a.active{color:#3d9be0}
.main-nav a.active::after{content:"";position:absolute;left:-8px;right:-8px;bottom:0;height:4px;background:#3d9be0}

/* hero */
.hero{position:absolute;left:0;top:106px;width:1200px;height:529px;overflow:hidden}
.hero-photo{position:absolute;inset:0;background:linear-gradient(90deg,#4d6a2c 0%,#6f8a3b 35%,#8a8f6a 60%,#b5ae95 80%,#5d6a3a 100%)}
.hero-copy{position:absolute;left:131px;top:164px;color:var(--white)}
.hero-kicker{font-family:"Montserrat",Arial,sans-serif;font-weight:400;font-size:29px;letter-spacing:.5px}
.hero-title{font-family:"Montserrat",Arial,sans-serif;font-weight:800;font-size:40px;line-height:46px;margin-top:4px}
.btn-pill{display:inline-flex;align-items:center;justify-content:center;border-radius:30px;font-family:"Montserrat",Arial,sans-serif;font-weight:700;text-decoration:none}
.hero-btn{position:absolute;left:138px;top:307px;width:175px;height:52px;background:#1a72c4;color:var(--white);font-size:16px}
.slide-arrow{position:absolute;top:226px}

/* about */
.about{position:absolute;left:0;top:635px;width:1200px;height:493px;background:#eef3f8;overflow:hidden}
.about-flag{position:absolute;inset:0;background:linear-gradient(100deg,#c9d7ef 0%,#e7d7dd 15%,#f2f5fa 35%,#f4f6fa 60%,#dfe6f3 80%,#c7d5ee 100%)}
.video-frame{position:absolute;left:116px;top:80px;width:478px;height:310px;background:radial-gradient(circle at 50% 45%,#10384f 0%,#070b16 70%);box-shadow:0 10px 30px rgba(0,0,0,.35)}
.video-play{position:absolute;left:198px;top:102px;width:76px;height:76px;border-radius:50%;background:var(--white)}
.video-play::after{content:"";position:absolute;left:30px;top:22px;border-left:24px solid #111;border-top:16px solid transparent;border-bottom:16px solid transparent}
.video-bar{position:absolute;left:0;bottom:0;width:100%;height:3px;background:#333}
.video-bar span{display:block;width:42%;height:100%;background:#aaa}
.about-title{position:absolute;left:653px;top:92px;font-family:"Montserrat",Arial,sans-serif;font-weight:800;font-size:28px;color:var(--navy-deep)}
.about-title em{font-style:normal;color:var(--red)}
.about-text{position:absolute;left:653px;top:150px;width:450px;font-size:15.5px;line-height:25px;color:#333}
.about-text p+p{margin-top:12px}
.btn-outline{position:absolute;left:653px;top:334px;width:162px;height:51px;border:3px solid var(--blue);color:var(--blue);font-size:14px;background:transparent}

/* pricing */
.pricing{position:absolute;left:0;top:1128px;width:1200px;height:613px;background:radial-gradient(ellipse at 50% 45%,var(--parchment-light) 0%,#e9d3a2 55%,#d6b670 100%)}
.section-kicker{position:absolute;width:100%;text-align:center;font-family:"Montserrat",Arial,sans-serif;font-weight:700;font-size:21px;color:var(--sky)}
.section-title{position:absolute;width:100%;text-align:center;font-family:"Montserrat",Arial,sans-serif;font-weight:800;font-size:28px;color:var(--navy-deep)}
.tier-card{position:absolute;left:104px;top:160px;width:481px;height:340px;background:rgba(255,255,255,.85);border-radius:8px;box-shadow:0 6px 18px rgba(0,0,0,.08)}
.tier{position:absolute;left:27px;width:423px;font-family:"Montserrat",Arial,sans-serif;font-weight:700;font-size:15px}
.tier-name{position:absolute;left:0;top:0}
.tier-size{position:absolute;right:0;top:2px}
.tier-bar{position:absolute;left:0;top:30px;width:423px;height:18px;border-radius:9px}
.tier.bronze{color:var(--bronze)} .tier.bronze .tier-bar{background:linear-gradient(90deg,#c58b68,#9a5a3b)}
.tier.silver{color:#8a8a8a} .tier.silver .tier-bar{background:var(--silver)}
.tier.gold{color:var(--gold)} .tier.gold .tier-bar{background:linear-gradient(90deg,#d8b93f,#b58f1c)}
.tier.platinum{color:var(--platinum)} .tier.platinum .tier-bar{background:linear-gradient(90deg,#22b2ef,#1485d4)}
.tier.diamond{color:var(--diamond)} .tier.diamond .tier-bar{background:linear-gradient(90deg,#1654a8,#0b2c6c)}
.promo{position:absolute;color:var(--white);font-family:"Montserrat",Arial,sans-serif}
.promo-family{left:607px;top:160px;width:463px;height:156px;background:linear-gradient(90deg,#e52d3b,#f0555a);border-radius:0 80px 0 80px;padding:34px 0 0 67px}
.promo-data{left:613px;top:346px;width:463px;height:158px;background:linear-gradient(90deg,#0b3e98,#0b6fc0);border-radius:80px 0 80px 0;padding:28px 0 0 72px}
.promo h3{font-weight:700;font-size:26px;letter-spacing:.5px}
.promo-family p{font-weight:700;font-size:20px;margin-top:12px}
.promo-data p{font-weight:400;font-size:15.5px;line-height:19px;margin-top:12px;width:340px}

/* packages */
.packages{position:absolute;left:0;top:1741px;width:1200px;height:594px;background:linear-gradient(180deg,#2c8fe3 0%,#67b3ef 35%,#bfe0f7 62%,#d8ecf9 75%,#9bb8dc 100%);overflow:hidden}
.packages-flag{position:absolute;left:0;bottom:0;width:1200px;height:210px;background:linear-gradient(90deg,#1d3f8f 0%,#c9333e 20%,#e7e7ef 35%,#c7dbf0 55%,#e7e7ef 75%,#c9333e 90%,#b22a36 100%);opacity:.85}
.package{position:absolute;width:199px;background:var(--white);text-align:center;box-shadow:0 4px 14px rgba(0,0,0,.12)}
.package-head{height:48px;line-height:48px;background:#e8eef6;font-family:"Montserrat",Arial,sans-serif;font-weight:600;font-size:17px;color:var(--navy-deep)}
.package-price{margin-top:22px;font-family:"Montserrat",Arial,sans-serif;font-weight:600;font-size:26px;color:var(--navy-deep)}
.package-price small{font-size:17px}
.package ul{list-style:none;margin-top:12px;font-size:14px;color:#444}
.package li{line-height:31px}
.btn-subscribe{margin:20px auto 0;width:131px;height:42px;border:2.5px solid var(--navy-deep);color:var(--navy-deep);font-size:12.5px}
.package.featured{background:var(--red);color:var(--white)}
.package.featured .package-head{background:#d72634;color:var(--white);height:48px}
.package.featured .package-price,.package.featured ul{color:var(--white)}
.package.featured .btn-subscribe{border-color:var(--white);color:var(--white);margin-top:40px}

/* location */
.location{position:absolute;left:0;top:2335px;width:1200px;height:491px;background:radial-gradient(ellipse at 55% 50%,var(--parchment-light) 0%,#e8d19f 55%,#d7b878 100%)}
.coverage-map{position:absolute;left:491px;top:45px;width:623px;height:390px;background:#1c1710;border-radius:38% 44% 30% 34%/30% 40% 46% 38%}
.search-card{position:absolute;left:115px;top:130px;width:355px;height:237px;background:var(--white);box-shadow:0 6px 18px rgba(0,0,0,.1);padding:42px 0 0 40px}
.search-card h2{font-family:"Montserrat",Arial,sans-serif;font-weight:800;font-size:23px;color:var(--navy-deep)}
.search-card p{margin-top:12px;font-size:13px;line-height:21px;color:var(--navy-deep);width:280px}
.search-field{position:absolute;left:32px;top:142px;width:299px;height:44px;border:2px solid var(--red);border-radius:24px;overflow:hidden;display:flex}
.search-field span{flex:1;padding-left:24px;line-height:40px;font-size:14px;color:#555}
.search-field i{width:40px;background:var(--red);display:flex;align-items:center;justify-content:center}

/* footer */
.site-footer{position:absolute;left:0;top:2826px;width:1200px;height:418px;background:radial-gradient(ellipse at 50% 40%,#1a4aa4 0%,#103a8c 55%,#0a2a6e 100%);color:var(--white)}
.footer-col{position:absolute;top:80px}
.footer-col h4{font-family:"Montserrat",Arial,sans-serif;font-weight:600;font-size:18px;margin-bottom:11px}
.footer-col a{display:block;color:var(--white);text-decoration:none;font-size:15px;line-height:25.4px}
.social{display:flex;gap:5px;margin-top:2px}
.social span{width:39px;height:39px;border:2px solid var(--white);border-radius:50%;display:block}
.copyright{position:absolute;left:0;top:372px;width:100%;text-align:center;font-size:12px}
</style>
</head>
<body>

<header class="site-header">
  <div class="brand"><span class="brand-dot"></span>TALLOW LINKWAVE</div>
  <nav class="main-nav">
    <a class="active" href="#">HOME</a>
    <a href="#">VIEW PLANS</a>
    <a href="#">ACTIVATE TODAY</a>
    <a href="#">CONTACT US</a>
    <a href="#">STEADY BEACON</a>
    <a href="#">MY ACCOUNT</a>
  </nav>
</header>

<section class="hero">
  <div class="hero-photo" role="img" aria-label="Soldier in camouflage uniform embracing a child holding a small American flag, garden background"></div>
  <div class="hero-copy">
    <div class="hero-kicker">WELCOME TO</div>
    <div class="hero-title">TALLOW LINKWAVE<br>MOBILE SERVICES</div>
  </div>
  <a class="btn-pill hero-btn" href="#">READ MORE</a>
  <svg class="slide-arrow" style="left:50px" width="26" height="40" viewBox="0 0 26 40"><path d="M20 4 6 20l14 16" fill="none" stroke="#fff" stroke-width="5"/></svg>
  <svg class="slide-arrow" style="left:1114px" width="26" height="40" viewBox="0 0 26 40"><path d="M6 4l14 16L6 36" fill="none" stroke="#fff" stroke-width="5"/></svg>
</section>

<section class="about">
  <div class="about-flag" role="img" aria-label="Faded stars and stripes flag backdrop"></div>
  <div class="video-frame" role="img" aria-label="Company commercial video">
    <div class="video-play"></div>
    <div class="video-bar"><span></span></div>
  </div>
  <h2 class="about-title"><em>ABOUT</em> TALLOW LINKWAVE</h2>
  <div class="about-text">
    <p>Augiat in pede Fusce tellus Sed metus augue convallis et vehicula ut pulvinar eu ante Integer orci tellus tristique vitae consequat nec mauris viverra in gravida eu mattis in ante</p>
    <p>Morbi eget arcurmentum vel congue id euismod in elit Fusce ultricies orci ac feugiat suscipit leo massa sodales velit et scelerisque mi tortor at ipsum Proin orci odio</p>
  </div>
  <a class="btn-pill btn-outline" href="#">READ MORE</a>
</section>

<section class="pricing">
  <div class="section-kicker" style="top:50px">OUR PRICING</div>
  <h2 class="section-title" style="top:78px">MOBILE SERVICES</h2>
  <div class="tier-card">
    <div class="tier bronze" style="top:20px"><span class="tier-name">BRONZE</span><span class="tier-size">100 MB</span><div class="tier-bar"></div></div>
    <div class="tier silver" style="top:80px;left:24px"><span class="tier-name">SILVER</span><span class="tier-size">1GB</span><div class="tier-bar"></div></div>
    <div class="tier gold" style="top:139px;left:24px"><span class="tier-name">GOLD</span><span class="tier-size">3GB</span><div class="tier-bar"></div></div>
    <div class="tier platinum" style="top:202px;left:24px"><span class="tier-name">PLATINUM</span><span class="tier-size">5GB</span><div class="tier-bar"></div></div>
    <div class="tier diamond" style="top:263px;left:24px"><span class="tier-name">DIAMOND</span><span class="tier-size">UNLIMITED</span><div class="tier-bar"></div></div>
  </div>
  <div class="promo promo-family">
    <h3>FAMILY PLAN</h3>
    <p>Buy 3 Lines get the 4th for FREE</p>
  </div>
  <div class="promo promo-data">
    <h3>DATA PLANS</h3>
    <p>Each Plan comes with Unlimited talk and text as well as 4G LTE Data. Unlimted Data is up to 30 GB</p>
  </div>
</section>

<section class="packages">
  <div class="packages-flag" role="img" aria-label="Waving American flag across a bright sky"></div>
  <h2 class="section-title" style="top:53px">OUR PACKAGES</h2>

  <div class="package" style="left:77px;top:160px;height:327px">
    <div class="package-head">BRONZE</div>
    <div class="package-price">$20<small>/month</small></div>
    <ul><li>Unlimited Talk</li><li>Unlimited Text</li><li>100 MB</li><li>4G LTE Data</li></ul>
    <a class="btn-pill btn-subscribe" href="#">SUBSCRIBE</a>
  </div>
  <div class="package featured" style="left:292px;top:129px;height:401px">
    <div class="package-head">SILVER</div>
    <div class="package-price">$25<small>/month</small></div>
    <ul><li>Data &amp; Voice</li><li>Unlimted Talk</li><li>Unlimited Text</li><li>1 GB</li><li>4G LTE Data</li></ul>
    <a class="btn-pill btn-subscribe" href="#">SUBSCRIBE</a>
  </div>
  <div class="package" style="left:511px;top:160px;height:327px">
    <div class="package-head">GOLD</div>
    <div class="package-price">$35<small>/month</small></div>
    <ul><li>Unlimited Talk</li><li>Unlimited Text</li><li>3GB</li><li>4G LTE Data</li></ul>
    <a class="btn-pill btn-subscribe" href="#">SUBSCRIBE</a>
  </div>
  <div class="package" style="left:730px;top:160px;height:327px">
    <div class="package-head">PLATINUM</div>
    <div class="package-price">$50<small>/month</small></div>
    <ul><li>Unlimited Talk</li><li>Unlimited Text</li><li>5GB</li><li>4G LTE Data</li></ul>
    <a class="btn-pill btn-subscribe" href="#">SUBSCRIBE</a>
  </div>
  <div class="package" style="left:944px;top:160px;height:327px">
    <div class="package-head">DIAMOND</div>
    <div class="package-price">$65<small>/month</small></div>
    <ul><li>Data &amp; Voice</li><li>Unlimited Talk</li><li>Unlimited Text</li><li>Up to 22 GB</li></ul>
    <a class="btn-pill btn-subscribe" href="#">SUBSCRIBE</a>
  </div>
</section>

<section class="location">
  <div class="coverage-map" role="img" aria-label="Distressed dark map of the United States showing coverage area"></div>
  <div class="search-card">
    <h2>SEARCH LOCATION</h2>
    <p>Lorem ipsum dolor sit amet consectetuer adipiscing elit Nam cursus Morbi</p>
    <div class="search-field">
      <span>Type Location</span>
      <i><svg width="12" height="18" viewBox="0 0 12 18"><path d="M2 2l7 7-7 7" fill="none" stroke="#fff" stroke-width="2.5"/></svg></i>
    </div>
  </div>
</section>

<footer class="site-footer">
  <div class="footer-col" style="left:162px">
    <h4>MAIN MENU</h4>
    <a href="#">Home</a><a href="#">Catalog</a><a href="#">View Plans</a><a href="#">Activate Today</a><a href="#">Contact Us</a><a href="#">Steady Beacon</a>
  </div>
  <div class="footer-col" style="left:380px">
    <h4>QUICK LINKS</h4>
    <a href="#">Terms &amp; Conditions</a><a href="#">Activating Your Service</a><a href="#">Acceptable Use Policy</a><a href="#">Wireless Privacy Policy</a><a href="#">Coverage Map</a>
  </div>
  <div class="footer-col" style="left:636px">
    <h4>CUSTOMER SUPPORT</h4>
    <a href="#">View Plans</a><a href="#">Contact Us</a><a href="#">Phone: +1 (833) 555-0142</a>
  </div>
  <div class="footer-col" style="left:917px">
    <h4>FOLLOW US</h4>
    <div class="social">
      <span aria-label="Social profile one"></span>
      <span aria-label="Social profile two"></span>
      <span aria-label="Social profile three"></span>
    </div>
  </div>
  <div class="copyright">© 2020 Company Name | All Rights Reserved | Disclaimer</div>
</footer>

</body>
</html>
```